Brookmere Osteopathy flyer

I want a clean clear DL flyer (but also want an A4 poster) promoting a new Osteopathic business in a semi rural area in Tasmania (Australia).
It can have pictures like the examples attached to show people what Osteopathy is (its like Chiropractic and physiotherapy).
I am the sole practioner and am male, so any pictures would be best to be a white male if possible.
I've attached some wording, you can use all, or none of it
I don't have a phone number for the business yet
info@brookmereosteopathy.example
www.brookmereosteopathy.example
Target Market(s)
Australians, from tradies, professionals, babies to retired people
Industry/Entity Type
Health
Look and feel

```html
<!DOCTYPE html>
<html lang="en">
<head>
<meta charset="utf-8">
<title>Brookmere Osteopathy flyer</title>
<link rel="stylesheet" href="https://fonts.googleapis.com/css2?family=Poppins:wght@300;400;600;700&display=swap">
<style>
  :root {
    --sky: #d6f1fc;
    --wave: #2ea6da;
    --panel: #0c96d2;
    --orange: #e87b1f;
    --ink: #1b1b1b;
    --white: #ffffff;
  }
  * { margin: 0; padding: 0; box-sizing: border-box; }
  html, body { width: 845px; height: 1200px; overflow: hidden; background: var(--white); }
  body { font-family: "Poppins", sans-serif; }
  .flyer { position: relative; width: 845px; height: 1200px; overflow: hidden; background: var(--white); }
  .backdrop { position: absolute; inset: 0; }
  .practitioner-photo {
    position: absolute; left: 52px; top: 14px; width: 350px; height: 576px;
    border-radius: 120px 120px 10px 10px;
    background:
      radial-gradient(ellipse 90px 110px at 50% 18%, rgba(201,165,138,0.85) 0%, rgba(201,165,138,0) 100%),
      linear-gradient(180deg, #5b4a40 0%, #b89478 12%, #e8dcd3 24%, #f7f7fa 40%, #eceef4 70%, #dfe3ec 100%);
  }
  .treatment-photo {
    position: absolute; width: 122px; height: 115px;
    border: 1.5px solid #2a2a2a;
  }
  .tone-back { background: linear-gradient(135deg, #f1ece8 0%, #d7b39a 50%, #3b4a6b 100%); }
  .tone-baby { background: linear-gradient(160deg, #8c7f7a 0%, #e6c9b8 40%, #4aa3d6 70%, #9fb0c8 100%); }
  .tone-spine { background: linear-gradient(135deg, #6a8fa8 0%, #d9a98a 50%, #f0d58a 100%); }
  .tone-shoulder { background: linear-gradient(150deg, #f3f5f7 0%, #dcae8d 45%, #c98f6e 100%); }
  .tone-neck { background: linear-gradient(140deg, #e9eef3 0%, #d3a487 50%, #2b2f38 100%); }
  .tone-stretch { background: linear-gradient(160deg, #e6e9ee 0%, #c99d82 40%, #2f3540 65%, #dfe6f0 100%); }
  .brand-seal {
    position: absolute; left: 648px; top: 398px; width: 172px; height: 172px;
    border: 2px solid var(--wave); border-radius: 50%;
    display: flex; align-items: center; justify-content: center; text-align: center;
    color: var(--panel); font-weight: 600; font-size: 17px; line-height: 1.25;
    background: var(--white);
  }
  .reasons-panel {
    position: absolute; left: 35px; top: 591px; width: 770px; height: 385px;
    background: var(--panel); border-radius: 62px 0 62px 0;
  }
  .reasons-frame {
    position: absolute; left: 23px; top: 21px; width: 728px; height: 338px;
    border: 2px solid var(--white); border-radius: 68px 0 68px 0;
  }
  .reasons-title {
    position: absolute; left: 0; right: 0; top: 55px; text-align: center;
    color: var(--white); font-weight: 700; font-size: 25px; letter-spacing: 0.1px;
  }
  .reasons-list { position: absolute; list-style: none; color: var(--white); font-weight: 300; font-size: 22.5px; line-height: 1.2; }
  .reasons-list li { position: absolute; left: 0; white-space: nowrap; }
  .reasons-list li::before {
    content: ""; position: absolute; left: -21px; top: 9px; width: 9px; height: 9px;
    border-radius: 50%; background: var(--white); box-shadow: inset -2px 0 0 #9fd4ee;
  }
  .reasons-list.left { left: 101px; top: 103px; }
  .reasons-list.right { left: 465px; top: 103px; }
  .reasons-list .note { font-size: 19px; display: block; line-height: 1.05; }
  .intro {
    position: absolute; left: 78px; width: 700px; top: 990px; text-align: center;
    color: var(--ink); font-size: 20.5px; line-height: 30px; font-weight: 400;
  }
  .contact-bar {
    position: absolute; left: 0; top: 1102px; width: 845px; height: 98px;
    background: var(--orange); border-radius: 50px 50px 0 0;
  }
  .contact-item {
    position: absolute; display: flex; align-items: center; gap: 10px;
    color: var(--white); font-size: 13.5px; font-weight: 400;
  }
  .contact-item svg { width: 20px; height: 20px; flex: none; }
</style>
</head>
<body>
<main class="flyer">
  <svg class="backdrop" viewBox="0 0 845 1200" width="845" height="1200" aria-hidden="true">
    <path d="M0,0 H845 V189 C760,212 700,262 600,350 C480,458 385,518 255,520 C150,522 60,482 0,440 Z" fill="var(--sky)"/>
    <path d="M845,189 C760,212 700,262 600,350 C480,458 385,518 255,520 C150,522 60,482 0,440 V462 C70,505 160,548 300,552 C430,556 510,500 620,405 C715,322 775,268 845,258 Z" fill="var(--wave)"/>
  </svg>

  <div class="practitioner-photo" role="img" aria-label="Photo of the osteopath in a white coat with a stethoscope, arms crossed"></div>

  <div class="treatment-photo tone-back" style="left:360px;top:28px" role="img" aria-label="Photo of lower back treatment"></div>
  <div class="treatment-photo tone-baby" style="left:454px;top:28px" role="img" aria-label="Photo of gentle head treatment for a baby"></div>
  <div class="treatment-photo tone-spine" style="left:549px;top:28px" role="img" aria-label="Photo of upper back manipulation"></div>
  <div class="treatment-photo tone-shoulder" style="left:401px;top:150px" role="img" aria-label="Photo of shoulder massage"></div>
  <div class="treatment-photo tone-neck" style="left:495px;top:150px" role="img" aria-label="Photo of neck and head treatment"></div>
  <div class="treatment-photo tone-stretch" style="left:451px;top:271px" role="img" aria-label="Photo of arm stretch on a treatment table"></div>

  <div class="brand-seal">Brookmere<br>Osteopathy</div>

  <section class="reasons-panel">
    <div class="reasons-frame"></div>
    <h2 class="reasons-title">COMMON REASONS PEOPLE VISIT AN OSTEOPATH</h2>
    <ul class="reasons-list left">
      <li style="top:0">Back / neck pain</li>
      <li style="top:38px">Headaches / migraines</li>
      <li style="top:76px">Joint and muscle pain</li>
      <li style="top:114px">Pregnancy-related<br>discomfort</li>
      <li style="top:183px">Disc related issues</li>
    </ul>
    <ul class="reasons-list right">
      <li style="top:0">Sciatica</li>
      <li style="top:38px">Plantar fasciitis</li>
      <li style="top:76px">Tendonitis / Bursitis</li>
      <li style="top:114px">Adhesive capsulitis<span class="note">(frozen shoulder)</span></li>
      <li style="top:183px">Tennis / Golfers elbow</li>
    </ul>
  </section>

  <p class="intro">Osteopaths use a combination of joint manipulation, targeted deep tissue massage and stretching to improve function, relieve pain and support the body’s ability to heal itself.</p>

  <footer class="contact-bar">
    <div class="contact-item" style="left:66px;top:30px">
      <svg viewBox="0 0 20 20"><path d="M10 1a6.5 6.5 0 0 0-6.5 6.5C3.5 12.5 10 19 10 19s6.5-6.5 6.5-11.5A6.5 6.5 0 0 0 10 1z" fill="#fff"/><circle cx="10" cy="7.5" r="2.4" fill="var(--orange)"/></svg>
      <span>48 Elm Creek Road, Brookmere</span>
    </div>
    <div class="contact-item" style="left:470px;top:30px">
      <svg viewBox="0 0 20 20" fill="none" stroke="#fff" stroke-width="1.5"><circle cx="10" cy="10" r="8.5"/><ellipse cx="10" cy="10" rx="3.8" ry="8.5"/><path d="M1.5 10h17M3 5.5h14M3 14.5h14"/></svg>
      <span>www.brookmereosteopathy.example</span>
    </div>
    <div class="contact-item" style="left:470px;top:63px">
      <svg viewBox="0 0 20 20" fill="none" stroke="#fff" stroke-width="1.5"><rect x="1" y="4" width="18" height="12"/><path d="M1 4l9 7 9-7M1 16l6.5-6M19 16l-6.5-6"/></svg>
      <span>info@brookmereosteopathy.example</span>
    </div>
  </footer>
</main>
</body>
</html>
```